Website design for legal tech start up in Switzerland (B2B)

We are for a legal tech start up in Switzerland called KOVA. We have been running since August 2016. This will be our first live website.

We need a website designed and business card design for our start-up in Switzerland. We also need the Web design to be converted into HTML and CSS files.

Function of website:
• To inform potential customers of our services
• Form a key part of our digital marketing and sales footprint.
• Branding

Please find attached logo.
Updates

Project Deadline Extended Reason: Giving us time to review submissions and provide opportunity for more submissions. Added Thursday, February 16, 2017

Project Deadline Extended
Reason: Looking for more idea's not necessarily set on blue and grey colours only.

Target Market(s)

B2B tech powered legal services.

Industry/Entity Type

Legal

Contact Information for Business Card

Lean and slick design.

Coding

Coded - Design and coding required

Number of Pages Required

5+ page

Requirements
Must have
• VERY LEAN AND CLEAN DESIGN!
• We have received many great standard designs, but we are looking for something more out-of-the box: You can get inspiration from these designs: http://www.pixelvane.com/websites/clean/
• Thanks!!
• Easy content management system
• Well structured coding for additional development
• Responsive webpage for all types of devices
• SEO optimized
• Tabs (Home, services, team, careers, blog, contact us)
• Colour scheme complementary to logo
Nice to have
• Look and Design - Approachable, High-tech, Modern
• Easy to add chat bot capability in future
Should not have
• Too busy/ too much clutter
• Not take to long to load

```html
<!DOCTYPE html>
<html lang="en">
<head>
<meta charset="utf-8">
<title>KOVA – Tech-Powered Legal Services</title>
<link href="https://fonts.googleapis.com/css2?family=Roboto:ital,wght@0,300;0,400;0,500;0,700;1,400&display=swap" rel="stylesheet">
<style>
:root{
  --navy:#1e3a6e;
  --blue:#2d5597;
  --accent:#3f74c4;
  --ink:#1b1f27;
  --text:#5a6270;
  --muted:#8a919c;
  --light:#f4f6f9;
  --rule:#d9dee6;
  --white:#fff;
}
*{box-sizing:border-box;margin:0;padding:0}
html,body{width:1200px;height:2609px;overflow:hidden}
body{font-family:"Roboto",Arial,sans-serif;color:var(--ink);background:var(--white);position:relative}
section,header,footer{position:absolute;left:0;width:1200px}
.dotline{position:absolute;border-top:2px dotted var(--accent)}

/* hero */
.hero{top:0;height:544px;overflow:hidden}
.hero-photo{position:absolute;inset:0;background:linear-gradient(105deg,#39414d 0%,#5f6670 32%,#434a55 58%,#6c737c 78%,#363d48 100%)}
.hero-shade{position:absolute;inset:0;background:linear-gradient(180deg,rgba(18,30,56,.55),rgba(18,30,56,.35))}
.topbar{position:absolute;top:0;left:0;width:1200px;height:66px;border-bottom:1px solid rgba(255,255,255,.22)}
.brand{position:absolute;left:54px;top:14px;font-size:34px;font-weight:500;letter-spacing:4px;color:var(--white)}
.nav{position:absolute;left:345px;top:24px;display:flex;gap:40px;list-style:none}
.nav li{color:var(--white);font-size:15px;font-weight:500;letter-spacing:.3px}
.btn-pill{position:absolute;top:16px;height:34px;border-radius:17px;font-size:13px;font-weight:500;display:flex;align-items:center;justify-content:center}
.btn-chat{left:970px;width:64px;border:2px solid var(--white);color:var(--white)}
.btn-eval{left:1038px;width:116px;background:var(--white);color:var(--ink)}
.hero-copy{position:absolute;left:370px;width:460px;top:228px;text-align:center;color:var(--white)}
.hero-copy h1{font-size:19px;font-weight:700;margin-bottom:14px}
.hero-copy p{font-size:11px;line-height:21px;opacity:.88}
.btn-outline{display:inline-block;margin-top:16px;border:1px solid var(--white);padding:10px 16px;font-size:12px;font-weight:500;letter-spacing:.5px}

/* contact strip */
.mailbar{top:544px;height:87px;background:var(--light)}
.mailbar svg{position:absolute;left:52px;top:28px}
.mail-label{position:absolute;left:113px;top:36px;font-size:13px;font-weight:500}
.field{position:absolute;top:28px;width:253px;height:34px;background:var(--white);border:1px solid var(--rule);border-radius:3px;font-size:12px;color:#9aa0a8;padding:10px 14px}
.btn-submit{position:absolute;left:1055px;top:28px;width:95px;height:34px;background:var(--navy);color:var(--white);font-size:13px;font-weight:500;border-radius:3px;display:flex;align-items:center;justify-content:center}

/* welcome */
.welcome{top:631px;height:200px}
.welcome-left{position:absolute;left:52px;width:530px;top:32px;text-align:center}
.welcome-brand{font-size:30px;font-weight:500;letter-spacing:4px;color:var(--navy);line-height:34px}
.welcome-left h2{font-size:21px;font-weight:700;border-bottom:2px dotted var(--accent);padding-bottom:6px;margin:2px 0 8px}
.welcome-left h2 span{color:var(--navy)}
.welcome-left p{font-size:13px;font-weight:500;line-height:20px}
.welcome-divider{position:absolute;left:599px;top:36px;width:2px;height:140px;background:var(--navy)}
.welcome-right{position:absolute;left:628px;width:520px;top:34px;font-size:12.5px;line-height:20px;color:var(--text);text-align:center}
.welcome-right p+p{margin-top:12px}

/* practice areas */
.practice{top:831px;height:282px;background:var(--light)}
.tabs{position:absolute;left:282px;top:12px;display:flex}
.tab{font-size:15px;font-weight:500;padding:12px 18px;border:2px solid transparent;margin-right:14px;border-radius:3px}
.tab.active{border-color:var(--navy);color:var(--navy);background:var(--white)}
.area{position:absolute;top:117px;width:252px;height:144px}
.area-photo{position:absolute;left:0;top:0;width:252px;height:112px;border-radius:3px}
.area-icon{position:absolute;left:103px;top:-26px;width:46px;height:46px;border-radius:50%;background:var(--navy);border:3px solid var(--white);display:flex;align-items:center;justify-content:center}
.area-label{position:absolute;left:10px;top:98px;width:232px;height:46px;background:var(--blue);color:var(--white);font-size:16px;font-weight:500;display:flex;align-items:center;justify-content:center;border-radius:3px}

/* statistics */
.stats{top:1139px;height:348px;color:var(--white);text-align:center;overflow:hidden}
.stats-photo{position:absolute;inset:0;background:linear-gradient(180deg,#6a6d72,#8b8e92 45%,#585b60)}
.stats-shade{position:absolute;inset:0;background:rgba(24,30,42,.5)}
.stats h2{position:absolute;top:18px;width:100%;font-size:33px;font-weight:400}
.stats-lead{position:absolute;top:96px;width:100%;font-size:17px;font-weight:300}
.stat{position:absolute;top:168px;width:320px}
.stat strong{display:block;font-size:32px;font-weight:400}
.stat span{display:block;font-size:18px;margin-top:4px}
.stat p{font-size:13px;font-weight:300;line-height:22px;margin-top:24px;opacity:.8}

/* blog */
.blog{top:1487px;height:464px}
.sec-title{position:absolute;width:100%;text-align:center;font-size:22px;font-weight:700}
.sec-title span{color:var(--navy)}
.post{position:absolute;top:83px;width:252px;height:355px;background:var(--light)}
.post-photo{width:252px;height:190px}
.post h3{font-size:17px;font-weight:700;margin:14px 18px 8px}
.post p{font-size:12.5px;line-height:19px;color:var(--muted);margin:0 18px}
.post-meta{position:absolute;left:18px;right:18px;top:318px;border-top:1px solid var(--rule);padding-top:12px;font-size:11px;color:var(--text);display:flex;justify-content:space-between;align-items:center}
.post-meta svg{vertical-align:-1px;margin-right:5px}

/* testimonials */
.testimonials{top:1951px;height:209px;background:var(--light)}
.quote{position:absolute;top:96px;width:416px;font-size:12.5px;line-height:20px;font-style:italic;color:var(--text)}
.quote-left{left:52px;text-align:right}
.quote-right{left:740px}
.quote cite{display:block;font-style:normal;color:var(--ink);font-size:13px;margin-top:6px}
.avatar{position:absolute;top:102px;width:76px;height:76px;border-radius:50%;border:3px solid var(--white)}
.quote-divider{position:absolute;left:599px;top:100px;height:80px;border-left:2px dotted #a0a6ae}

/* social strip */
.likebar{top:2160px;height:75px}
.likebar-rule{position:absolute;left:52px;width:1096px;top:37px;border-top:1px solid var(--rule)}
.likebox{position:absolute;left:375px;top:14px;width:450px;height:46px;border:1px solid var(--rule);border-radius:23px;background:var(--white)}
.likebox-thumb{position:absolute;left:0;top:0;width:60px;height:44px;border-right:1px solid var(--rule);display:flex;align-items:center;justify-content:center}
.like-btn{position:absolute;left:122px;top:14px;width:44px;height:18px;background:var(--accent);color:var(--white);font-size:10px;font-weight:700;border-radius:2px;display:flex;align-items:center;justify-content:center}
.like-text{position:absolute;left:174px;top:16px;font-size:10px;color:#333}

/* footer */
.site-footer{top:2235px;height:374px;background:linear-gradient(90deg,var(--blue),#4a7bc2);color:var(--white)}
.f-col{position:absolute;top:20px}
.f-col h4{font-size:18px;font-weight:500;margin-bottom:18px}
.f-col p{font-size:12.5px;line-height:20px}
.f-col p+p{margin-top:14px}
.f-contact{left:52px;width:250px}
.f-hq{left:333px;width:535px;text-align:center}
.f-about{left:896px;width:252px}
.map{width:535px;height:224px;background:linear-gradient(135deg,#d3dbcc,#b2cbe6 45%,#e6e0d2)}
.socials{display:flex;gap:12px;margin-top:14px}
.socials i{display:block;width:12px;height:12px;border-radius:50%;background:var(--white)}
.f-bottom{position:absolute;left:52px;width:1096px;top:310px;border-top:1px solid rgba(255,255,255,.4);height:64px;font-size:12px;font-weight:500}
.f-bottom .copy{position:absolute;left:0;top:26px}
.f-bottom .rights{position:absolute;right:0;top:26px}
.f-brand{position:absolute;left:448px;width:200px;text-align:center;top:14px;font-size:30px;font-weight:500;letter-spacing:4px}
</style>
</head>
<body>

<header class="hero">
  <div class="hero-photo" role="img" aria-label="Photo of business lawyers in conversation"></div>
  <div class="hero-shade"></div>
  <div class="topbar">
    <div class="brand">KOVA</div>
    <ul class="nav"><li>HOME</li><li>SERVICES</li><li>TEAM</li><li>CAREERS</li><li>BLOG</li><li>CONTACT</li></ul>
    <div class="btn-pill btn-chat">Chat</div>
    <div class="btn-pill btn-eval">Free Evaluation</div>
  </div>
  <div class="hero-copy">
    <h1>Tech-Powered Legal Help for Business</h1>
    <p>Smart legal workflows for in-house teams across Switzerland. Clear fixed pricing, fast answers and secure digital tools that keep your contracts moving.</p>
    <span class="btn-outline">LEARN MORE</span>
  </div>
</header>

<section class="mailbar">
  <svg width="36" height="32" viewBox="0 0 36 32"><path d="M2 15 L34 2 L26 30 L17 20 Z M17 20 L34 2 M17 20 L16 29 L21 24" fill="none" stroke="#1e3a6e" stroke-width="2.2" stroke-linejoin="round"/></svg>
  <div class="mail-label">Feel Free to Mail</div>
  <div class="field" style="left:238px">Full Name *</div>
  <div class="field" style="left:510px">Phone Number *</div>
  <div class="field" style="left:782px">Your Email *</div>
  <div class="btn-submit">SUBMIT</div>
</section>

<section class="welcome">
  <div class="welcome-left">
    <div class="welcome-brand">KOVA</div>
    <h2>Welcome! <span>We’re Kova Legal Tech</span></h2>
    <p>We have more than 30 years experience in law.<br>We have a range of services to help in-house lawyers. Take a look and see how we can help you and your team.</p>
  </div>
  <div class="welcome-divider"></div>
  <div class="welcome-right">
    <p>We combine experienced Swiss lawyers with modern software, so routine legal work is handled quickly, transparently and at a predictable cost for your business.</p>
    <p>From contract review to compliance checks, our platform keeps every matter organised in one secure place, and your team always knows the next step.</p>
  </div>
</section>

<section class="practice">
  <div class="tabs">
    <div class="tab active">Criminal Charges</div>
    <div class="tab">Estate Planning</div>
    <div class="tab">In House legal</div>
    <div class="tab">Personal Injury</div>
  </div>
  <div class="dotline" style="left:36px;width:1128px;top:72px"></div>

  <div class="area" style="left:52px">
    <div class="area-photo" role="img" aria-label="Photo of handcuffed hands" style="background:linear-gradient(135deg,#7a5b4c,#bf9782,#5c4238)"></div>
    <div class="area-icon"><svg width="22" height="22" viewBox="0 0 22 22"><path d="M4 14 L12 6 M9 3 L15 9 M2 20 H12" stroke="#fff" stroke-width="2.6" fill="none" stroke-linecap="round"/></svg></div>
    <div class="area-label">Criminal Charges</div>
  </div>
  <div class="area" style="left:333px">
    <div class="area-photo" role="img" aria-label="Photo of a small wooden house model on documents" style="background:linear-gradient(135deg,#e6dcc2,#c8a972,#efe8d6)"></div>
    <div class="area-icon"><svg width="22" height="22" viewBox="0 0 22 22"><path d="M3 11 L11 4 L19 11 V19 H3 Z" fill="#fff"/><rect x="9" y="13" width="4" height="6" fill="#1e3a6e"/></svg></div>
    <div class="area-label">Estate Planning</div>
  </div>
  <div class="area" style="left:614px">
    <div class="area-photo" role="img" aria-label="Photo of office towers against blue sky" style="background:linear-gradient(180deg,#5f8fd0,#a9c4e6,#6d7b8c)"></div>
    <div class="area-icon"><svg width="22" height="22" viewBox="0 0 22 22"><rect x="3" y="12" width="4" height="7" fill="#fff"/><rect x="9" y="8" width="4" height="11" fill="#fff"/><rect x="15" y="4" width="4" height="15" fill="#fff"/></svg></div>
    <div class="area-label">Capital Market</div>
  </div>
  <div class="area" style="left:895px">
    <div class="area-photo" role="img" aria-label="Photo of a distressed driver after a car accident" style="background:linear-gradient(135deg,#977a6c,#46597d,#2b3a5c)"></div>
    <div class="area-icon"><svg width="24" height="22" viewBox="0 0 24 22"><path d="M3 14 L5 8 H19 L21 14 V17 H3 Z" fill="#fff"/><circle cx="7" cy="17" r="2" fill="#1e3a6e"/><circle cx="17" cy="17" r="2" fill="#1e3a6e"/></svg></div>
    <div class="area-label">Personal Injury</div>
  </div>
</section>

<section class="stats">
  <div class="stats-photo" role="img" aria-label="Photo of classical stone columns of a courthouse"></div>
  <div class="stats-shade"></div>
  <h2>Law Firm Statistics</h2>
  <p class="stats-lead">Numbers from our first years of helping Swiss companies work faster with legal technology.</p>
  <div class="stat" style="left:64px"><strong>3541</strong><span>Working Hours</span><p>Hours saved for in-house teams through automated drafting and review.</p></div>
  <div class="stat" style="left:440px"><strong>4689</strong><span>Legal Issues</span><p>Contracts, filings and compliance questions resolved on our platform.</p></div>
  <div class="stat" style="left:816px"><strong>2349</strong><span>Satisfied Clients</span><p>Businesses that trust us with everyday legal work and growth.</p></div>
</section>

<section class="blog">
  <h2 class="sec-title" style="top:12px">Latest <span>Blog &amp; Posts</span></h2>
  <div class="dotline" style="left:52px;width:1096px;top:51px"></div>

  <article class="post" style="left:52px">
    <div class="post-photo" role="img" aria-label="Photo of a person walking with a backpack" style="background:linear-gradient(135deg,#6a4b36,#ad8562,#3b3c46)"></div>
    <h3>Standard Post</h3>
    <p>Enim congue blandit. Lorem ipsum dolor sit amet, consectetur adipiscing elit. Quisque…</p>
    <div class="post-meta"><span><svg width="10" height="10" viewBox="0 0 10 10"><rect x="0.5" y="1.5" width="9" height="8" fill="none" stroke="#5a6270"/><path d="M0.5 4 H9.5" stroke="#5a6270"/></svg>22 June, 2015</span><span>0</span></div>
  </article>
  <article class="post" style="left:333px">
    <div class="post-photo" role="img" aria-label="Photo of a coffee carafe on a table" style="background:linear-gradient(135deg,#d8d4cc,#a49a8c,#e8e4dc)"></div>
    <h3>Video Post</h3>
    <p>Ultrices posuere cubilia curae curabitur sit amet tortor ut massa commodo. Vestibulum…</p>
    <div class="post-meta"><span><svg width="10" height="10" viewBox="0 0 10 10"><rect x="0.5" y="1.5" width="9" height="8" fill="none" stroke="#5a6270"/><path d="M0.5 4 H9.5" stroke="#5a6270"/></svg>22 June, 2015</span><span>0</span></div>
  </article>
  <article class="post" style="left:614px">
    <div class="post-photo" role="img" aria-label="Photo of a café interior with brick wall" style="background:linear-gradient(135deg,#7a4b35,#bfa07d,#5a3b2b)"></div>
    <h3>Post with Image</h3>
    <p>Enim congue blandit. Lorem ipsum dolor sit amet, consectetur adipiscing elit. Quisque…</p>
    <div class="post-meta"><span><svg width="10" height="10" viewBox="0 0 10 10"><rect x="0.5" y="1.5" width="9" height="8" fill="none" stroke="#5a6270"/><path d="M0.5 4 H9.5" stroke="#5a6270"/></svg>22 June, 2015</span><span>0</span></div>
  </article>
  <article class="post" style="left:895px">
    <div class="post-photo" role="img" aria-label="Photo of a leather wallet on patterned fabric" style="background:linear-gradient(135deg,#b0a090,#6a5040,#c8bcae)"></div>
    <h3>Image Post</h3>
    <p>Ultrices posuere cubilia curae curabitur sit amet tortor ut massa commodo. Vestibulum…</p>
    <div class="post-meta"><span><svg width="10" height="10" viewBox="0 0 10 10"><rect x="0.5" y="1.5" width="9" height="8" fill="none" stroke="#5a6270"/><path d="M0.5 4 H9.5" stroke="#5a6270"/></svg>22 June, 2015</span><span>3</span></div>
  </article>
</section>

<section class="testimonials">
  <h2 class="sec-title" style="top:16px">What <span>People Say</span></h2>
  <div class="dotline" style="left:52px;width:1096px;top:56px"></div>
  <blockquote class="quote quote-left">Kova turned weeks of contract back-and-forth into a few days. The platform is simple, the lawyers are responsive and the pricing is always clear to our finance team.<cite>Marc Huber, Operations Manager</cite></blockquote>
  <div class="avatar" style="left:490px;background:linear-gradient(135deg,#d2b49a,#8a6b54)" role="img" aria-label="Portrait of Marc Huber"></div>
  <div class="quote-divider"></div>
  <div class="avatar" style="left:632px;background:linear-gradient(135deg,#c49878,#6b4b3b)" role="img" aria-label="Portrait of Nora Keller"></div>
  <blockquote class="quote quote-right">We finally have one place for every legal request. Our team files a question in minutes and gets expert answers fast, without the usual paperwork and delays.<cite>Nora Keller, Creative Designer</cite></blockquote>
</section>

<section class="likebar">
  <div class="likebar-rule"></div>
  <div class="likebox">
    <div class="likebox-thumb"><svg width="16" height="16" viewBox="0 0 16 16"><path d="M2 7 H5 V14 H2 Z M5 7 L8 2 C9.5 2 9.5 4 9 6 H13.5 C14.5 6 15 7 14.6 8 L13 13 C12.7 13.7 12 14 11.5 14 H5" fill="none" stroke="#b0b6be" stroke-width="1.3"/></svg></div>
    <div class="like-btn">✓ Like</div>
    <div class="like-text">You and 4k others like this.</div>
  </div>
</section>

<footer class="site-footer">
  <div class="f-col f-contact">
    <h4>Contact Us</h4>
    <p>Please feel free to contact us for any issue. Our staff is available to you from 9AM until 5PM on weekdays.</p>
    <p><b>Phone:</b> +41 44 512 30 80</p>
    <p><b>Office:</b> Company Address Here</p>
    <p><b>Email:</b> hello@kova-legal.ch</p>
    <div class="socials"><i></i><i></i><i></i><i></i><i></i></div>
  </div>
  <div class="f-col f-hq">
    <h4>Headquarters</h4>
    <div class="map" role="img" aria-label="Street map showing the office location"></div>
  </div>
  <div class="f-col f-about">
    <h4>About Team</h4>
    <p>A small team of Swiss lawyers, engineers and designers building legal services that feel as simple as the software your business already uses every day.</p>
    <p>We started in August 2016 with one goal: make quality legal help faster, clearer and more affordable for growing companies.</p>
  </div>
  <div class="f-bottom">
    <span class="copy">Copyright © Kova</span>
    <span class="f-brand">KOVA</span>
    <span class="rights">All rights reserved</span>
  </div>
</footer>

</body>
</html>
```